Verodex business card

Business card for sustainable investment company called "Verodex". Verodex is an exchange platform selling carbon credits between buyers and sellers. Carbon Credits are an environmental commodity for reducing global carbon emissions.

the card should obviously have our logo and the theme should be sustainability/environment mixed with a trading platform.

Contact Information for Business Card

Logo, Name, Title, Phone, Email

Colors
0054AA
0677BA
7BADD7
CADEEF
E8F1F8
0094D4
00A9DD
6FCCEA
C7EBF8
E9F6FB
00AB8E
00BBA5
67D7C9
C6EFE9
E9F9F6
59FF00
82FF00
B8FF75
E3FFCB
F4FFEA

```html
<!DOCTYPE html>
<html lang="en">
<head>
<meta charset="utf-8">
<title>Verodex business card</title>
<link href="https://fonts.googleapis.com/css2?family=Sora:wght@400;600&display=swap" rel="stylesheet">
<style>
  :root {
    --backdrop: #e4e4e2;
    --navy: #1f2f4d;
    --navy-deep: #17233b;
    --ink: #1a2540;
    --card-light: #f3f3f3;
    --teal: #4fb8c9;
    --blue: #3f6fc4;
    --accent: #2f7fc4;
  }
  * { margin: 0; padding: 0; box-sizing: border-box; }
  html, body { width: 1200px; height: 1200px; overflow: hidden; }
  body {
    background: var(--backdrop);
    font-family: "Sora", sans-serif;
    color: var(--ink);
    position: relative;
  }
  .card {
    position: absolute;
    left: 234px;
    width: 731px;
    height: 417px;
    box-shadow: 0 14px 28px rgba(0,0,0,0.18);
  }
  .card-back {
    top: 160px;
    background: linear-gradient(90deg, var(--navy-deep), #2c3f5e);
  }
  .card-front {
    top: 632px;
    background: linear-gradient(110deg, #f7f7f7, var(--card-light) 60%, #e9e9e9);
  }
  .edge-strip { position: absolute; right: 0; width: 21px; }
  .edge-strip.top { top: 0; height: 165px; background: var(--navy); border-bottom-left-radius: 10px; }
  .edge-strip.middle { top: 178px; height: 60px; background: linear-gradient(180deg, var(--teal), var(--blue)); border-radius: 10px 0 0 10px; }
  .edge-strip.bottom { top: 251px; height: 166px; background: var(--navy); border-top-left-radius: 10px; }
  .brand { position: absolute; left: 56px; top: 52px; display: flex; align-items: center; gap: 18px; }
  .brand-square { width: 54px; height: 54px; background: var(--accent); }
  .brand-name { font-size: 42px; font-weight: 600; color: var(--ink); letter-spacing: 0.5px; line-height: 1; }
  .person { position: absolute; right: 56px; top: 168px; text-align: right; }
  .person-name {
    font-size: 36px; font-weight: 600; line-height: 1;
    background: linear-gradient(90deg, var(--teal), var(--blue));
    -webkit-background-clip: text; background-clip: text; color: transparent;
  }
  .person-title { font-size: 19px; margin-top: 10px; line-height: 1; }
  .address { position: absolute; left: 56px; top: 224px; font-size: 19px; line-height: 27px; }
  .contacts { position: absolute; left: 56px; top: 284px; list-style: none; font-size: 19px; }
  .contacts li { display: flex; align-items: center; gap: 7px; height: 28px; }
  .contacts svg { width: 16px; height: 16px; fill: var(--accent); }
</style>
</head>
<body>
  <div class="card card-back" role="img" aria-label="Dark navy card back with embossed repeating brand symbol pattern"></div>

  <div class="card card-front">
    <div class="brand">
      <div class="brand-square"></div>
      <div class="brand-name">VERODEX</div>
    </div>

    <div class="person">
      <div class="person-name">Marek Halden</div>
      <div class="person-title">Sales Representative</div>
    </div>

    <div class="address">
      Verodex Head Office<br>
      Budapest XIII. Nádfonó utca 18.
    </div>

    <ul class="contacts">
      <li>
        <svg viewBox="0 0 24 24" aria-hidden="true"><path d="M6.6 10.8a15.1 15.1 0 0 0 6.6 6.6l2.2-2.2a1 1 0 0 1 1-.25 11.4 11.4 0 0 0 3.6.57 1 1 0 0 1 1 1V20a1 1 0 0 1-1 1A17 17 0 0 1 3 4a1 1 0 0 1 1-1h3.5a1 1 0 0 1 1 1c0 1.25.2 2.45.57 3.57a1 1 0 0 1-.25 1z"/></svg>
        +36 30 482 1957
      </li>
      <li>
        <svg viewBox="0 0 24 24" aria-hidden="true"><path d="M2 5h20v14H2z M2 5l10 8 10-8" fill="var(--accent)"/><path d="M2 5l10 8 10-8" fill="none" stroke="#f3f3f3" stroke-width="1.6"/></svg>
        szerviz@verodex.com
      </li>
      <li>
        <svg viewBox="0 0 24 24" aria-hidden="true"><circle cx="12" cy="12" r="10"/><path d="M2 12h20M12 2c3 3 3 17 0 20M12 2c-3 3-3 17 0 20" fill="none" stroke="#f3f3f3" stroke-width="1.4"/></svg>
        www.verodex.com
      </li>
    </ul>

    <div class="edge-strip top"></div>
    <div class="edge-strip middle"></div>
    <div class="edge-strip bottom"></div>
  </div>
</body>
</html>
```